Business Card Design Project

We are looking for a new business card design to go with our new logo. We need to have a front and back card with our name and numberous phone numbers on the front and our addresses on the back. We will need to be able to edit the cards to have different names and numbers. Right now our card looks too busy and cluttered. We need to have our Brightmoor Estates Group Logo Prominently displayed. We will also need the Halvern Dunstead Portland Central, the relator logo and the equal housing logo on the front somewhere. We would like to have our addresses on the back along with the quote "Our most important goal is to exceed the expectations of our clients and the finest compliment we can received is a referral from a friend or past client. Thank you for your support!" Also, we would like the "Please follow us on : facebook logo, twitter loto, youtube logo and wordpress logo" I've attached our new logo and what our current business card looks like.

```html
<!DOCTYPE html>
<html lang="en">
<head>
<meta charset="utf-8">
<title>Brightmoor Estates Group – Business Cards</title>
<link href="https://fonts.googleapis.com/css2?family=EB+Garamond:ital,wght@0,400;0,600;0,700;1,400&display=swap" rel="stylesheet">
<style>
  :root {
    --brand-red: #b8282e;
    --ink: #1e1e1e;
    --muted: #7a7a7a;
    --paper: #ffffff;
    --backdrop: #ece8e2;
    --badge: #5a5a5a;
  }
  * { box-sizing: border-box; margin: 0; padding: 0; }
  html, body { width: 1200px; height: 1000px; overflow: hidden; }
  body {
    background: var(--backdrop);
    font-family: "EB Garamond", Georgia, serif;
    color: var(--ink);
    position: relative;
  }
  .card {
    position: absolute;
    top: 230px;
    width: 340px;
    height: 540px;
    background: var(--paper);
    box-shadow: 0 6px 18px rgba(0,0,0,.18);
    overflow: hidden;
  }
  .card--back { left: 220px; }
  .card--front { left: 640px; }

  /* Brand mark */
  .brand { display: flex; align-items: center; justify-content: center; gap: 10px; }
  .brand__dot { width: 22px; height: 22px; border-radius: 50%; background: var(--brand-red); flex: none; }
  .brand__name { font-weight: 600; color: var(--ink); line-height: 1; letter-spacing: .5px; text-align: center; }

  /* Back card (addresses) */
  .card--back .brand { position: absolute; top: 150px; left: 0; right: 0; }
  .card--back .brand__name { font-size: 27px; }
  .back__panel {
    position: absolute; top: 210px; left: 0; right: 0; bottom: 0;
    background: var(--brand-red); color: var(--paper); text-align: center;
    padding: 22px 34px 0;
  }
  .back__quote { font-style: italic; font-size: 12.5px; line-height: 1.25; }
  .back__address { margin-top: 36px; font-size: 15px; font-weight: 600; line-height: 1.2; }
  .back__follow { margin-top: 44px; font-size: 14px; font-weight: 600; }
  .social { display: flex; justify-content: center; gap: 12px; margin-top: 10px; }
  .social__tile { width: 34px; height: 34px; border-radius: 5px; background: rgba(255,255,255,.85); }

  /* Front card (contact) */
  .card--front .brand { position: absolute; top: 186px; left: 0; right: 0; }
  .card--front .brand__dot { width: 16px; height: 16px; }
  .card--front .brand__name { font-size: 21px; }
  .affiliations { position: absolute; top: 232px; left: 0; right: 0; display: flex; justify-content: center; align-items: center; gap: 16px; }
  .affiliations__partner { width: 70px; height: 12px; background: var(--brand-red); }
  .affiliations__mark { width: 22px; height: 22px; background: var(--badge); }
  .agent { position: absolute; top: 285px; left: 40px; }
  .agent__name { color: var(--brand-red); font-size: 22px; font-weight: 600; line-height: 1.05; }
  .agent__title { color: var(--muted); font-size: 14px; }
  .phones { position: absolute; top: 350px; left: 40px; list-style: none; font-size: 15px; font-weight: 600; line-height: 1.2; }
  .phones__label { color: var(--brand-red); font-weight: 400; }
  .links { position: absolute; top: 438px; left: 40px; font-size: 14.5px; font-weight: 700; line-height: 1.25; }
  .front__band { position: absolute; left: 0; right: 0; bottom: 0; height: 28px; background: var(--brand-red); }
</style>
</head>
<body>

  <section class="card card--back" aria-label="Card back with addresses">
    <div class="brand">
      <span class="brand__dot"></span>
      <span class="brand__name">Brightmoor<br><small style="font-size:13px;letter-spacing:2px;">ESTATES GROUP</small></span>
    </div>
    <div class="back__panel">
      <p class="back__quote">“Our most important goal is to exceed the expections of our clients and the finest compliment we can recieve is a referral from a friend or past client. Thank you for your support!”</p>
      <p class="back__address">118 Harbor Commons<br>2750 SE Alder Road, #300<br>Portland, OR 97222</p>
      <p class="back__follow">Please follow us on:</p>
      <div class="social" aria-label="Social channels">
        <span class="social__tile"></span>
        <span class="social__tile"></span>
        <span class="social__tile"></span>
        <span class="social__tile"></span>
      </div>
    </div>
  </section>

  <section class="card card--front" aria-label="Card front with contact details">
    <div class="brand">
      <span class="brand__dot"></span>
      <span class="brand__name">Brightmoor<br><small style="font-size:10px;letter-spacing:2px;">ESTATES GROUP</small></span>
    </div>
    <div class="affiliations" aria-label="Halvern Dunstead Portland Central and housing badges">
      <span class="affiliations__partner"></span>
      <span class="affiliations__mark"></span>
      <span class="affiliations__mark"></span>
    </div>
    <div class="agent">
      <p class="agent__name">Lena Marlowe</p>
      <p class="agent__title">Broker, Listings Specialist</p>
    </div>
    <ul class="phones">
      <li>(503) 555-0142 <span class="phones__label">cell</span></li>
      <li>(503) 555-0128 <span class="phones__label">office</span></li>
      <li>(800) 555-0187 <span class="phones__label">toll free</span></li>
      <li>(503) 555-0163 <span class="phones__label">fax</span></li>
    </ul>
    <p class="links">lena@brightmoorestates.com<br>www.brightmoorestates.com</p>
    <div class="front__band"></div>
  </section>

</body>
</html>
```